International Petrochemical business needs a web design for Clearway Desk system

We need a web design for a "Clearway Desk" system for an international petrochemical company. The web site is used internally within the company. It is hosted by an internal department which provides government permit request service for other departments.

We would like to see designs of two pages using color light blue. (home page, internal page as attached).
Home Page:
1. Header has a background image and small animation. Header on home page can be taller than the header of the internal page.
2. Layout as attached.

Internal Page:
1. Header can use the same background image as the home page and can be shorter to utilize the page for content.
2. The blue icon behind every captions represent an icon. When user move mouse over this icon, it displays the caption in Thai language as a tooltip. This icon needs to be redesign.

The final design should communicate the followings:
- Excellent service provided system in terms of time and accurary
- Rapid growth of business via building petrochemical refinery plant
Updates

For Internal Page, the blue circle behind every captions represent an icon. When mouse over this icon, a tool tip showing the caption in Thai language is shown. Please also design this icon..

There are more feedbacks from customer as followed:

1. Banner should consists of 
    1.1 "Approved" stamp on paper
    1.2 An image of Garuda. It is used on every government documents in Thailand
    1.3 Image of petrochemical plant
2. Each menu item (Home, Permit, Search, etc) should have different colors. Drop down menu will use the same color as its parent menu item.
3. Overall tone of the web page should be light blue with background of the body the web page in white
4. "New Request" button should use green color with icon on it
5. Table header of each box in the body of the page should use dark blue background with text in white

Please kindly submit your revisions.
Thank you.

Industry/Entity Type

Business

Requirements
Must have
• 1. Design for 1024x768 screen resolution
2. Use light blue theme
3. Background of header where the company logo is must have white background

```html
<!DOCTYPE html>
<html lang="en">
<head>
<meta charset="utf-8">
<title>Clearway Desk – Home</title>
<link href="https://fonts.googleapis.com/css2?family=Ubuntu:wght@400;500;700&family=Roboto:wght@400;500&display=swap" rel="stylesheet">
<style>
  :root{
    --page-bg:#f2f2f2;
    --card-bg:#ffffff;
    --card-edge:#5bc8f0;
    --card-shadow:#1a7fd0;
    --navy:#1c3a6e;
    --panel-head:#274b82;
    --col-head:#1ab4ec;
    --pager-bar:#7a9abb;
    --divider:#9bb0c8;
    --link:#1a6fd6;
    --text:#222;
    --go:#00c000;
    --nav-home:#1fb5ea;
    --nav-permits:#f0b400;
    --nav-search:#6cc04a;
    --nav-report:#e0413a;
    --nav-admin:#8a5aa8;
    --nav-help:#5a7aa8;
    --menu-light:#1fb5ea;
    --menu-dark:#2a5690;
  }
  *{box-sizing:border-box;margin:0;padding:0}
  html,body{width:1171px;height:1200px;overflow:hidden;background:var(--page-bg)}
  body{font-family:"Roboto",Arial,sans-serif;color:var(--text)}
  .stage{position:relative;width:1000px;height:1025px;transform:scale(1.171);transform-origin:0 0}
  .abs{position:absolute}

  .card-shadow{left:62px;top:28px;width:876px;height:924px;background:var(--card-shadow)}
  .card{left:54px;top:12px;width:872px;height:928px;background:var(--card-bg);border:1px solid var(--card-edge)}

  .brand{left:105px;top:38px;display:flex;align-items:center;gap:8px;font-family:"Ubuntu",sans-serif;font-weight:700;font-size:17px;color:#1a8fe0;line-height:1}
  .brand-dot{width:30px;height:30px;border-radius:50%;background:#1a8fe0}
  .system-name{right:96px;top:27px;font-family:"Ubuntu",sans-serif;font-weight:700;font-size:22px;color:var(--navy);letter-spacing:.5px}

  .nav{left:550px;top:68px;display:flex;font-family:"Ubuntu",sans-serif;font-size:11px;color:var(--navy)}
  .nav a{display:block;text-align:center;padding:0 0 6px;border-bottom:3px solid;color:inherit;text-decoration:none}
  .nav .home{width:58px;border-color:var(--nav-home)}
  .nav .permits{width:60px;border-color:var(--nav-permits)}
  .nav .search{width:60px;border-color:var(--nav-search)}
  .nav .report{width:60px;border-color:var(--nav-report)}
  .nav .admin{width:60px;border-color:var(--nav-admin)}
  .nav .help{width:58px;border-color:var(--nav-help)}

  .dropdown{left:550px;top:91px;width:118px;font-family:"Ubuntu",sans-serif;font-size:10px;color:#fff;z-index:2}
  .dropdown div{height:23px;line-height:23px;padding-left:9px;background:var(--menu-light)}
  .dropdown div.alt{background:var(--menu-dark)}

  .banner{left:77px;top:98px;width:831px;height:214px;background:linear-gradient(100deg,#6f7e8c 0%,#b9c4cc 35%,#8fa6b8 60%,#cfe3f2 100%)}

  .panel{position:absolute;border:1px solid var(--panel-head);background:#fff;display:flex;flex-direction:column}
  .panel-title{background:var(--panel-head);color:#fff;font-family:"Ubuntu",sans-serif;font-weight:700;font-size:15px;height:38px;line-height:38px;padding-left:11px;letter-spacing:.3px}
  .row{display:grid;grid-template-columns:var(--cols)}
  .row-head{background:var(--col-head);height:30px;font-family:"Ubuntu",sans-serif;font-size:12px;color:#10233f}
  .row-head span{line-height:30px;padding-left:11px;border-right:1px solid #fff}
  .row-body{flex:1;font-size:10.5px;line-height:16px}
  .row-body span{padding:8px 0 0 11px;border-right:1px solid var(--divider)}
  .row span:last-child{border-right:0}
  .row-body a{color:var(--link);text-decoration:underline}
  .row-body .pad{padding-left:17px}
  .pager{height:28px;background:var(--pager-bar);display:flex;justify-content:flex-end;align-items:center;gap:1px;padding-right:7px}
  .pager span{width:16px;height:16px;border:1px solid #fff;background:var(--navy);color:#fff;font-size:9px;line-height:14px;text-align:center}
  .pager span.on{background:var(--col-head)}

  .dot{display:inline-block;width:11px;height:11px;border-radius:50%;vertical-align:-2px;margin-right:5px}
  .dot.red{background:radial-gradient(circle at 35% 35%,#ff8a80,#d90f0f)}
  .dot.amber{background:radial-gradient(circle at 35% 35%,#fff59a,#f0b400)}

  .new-request{left:501px;top:684px;width:407px;height:45px;background:var(--go);color:#fff;font-family:"Ubuntu",sans-serif;font-weight:700;font-size:19px;display:flex;align-items:center;justify-content:center;gap:10px;letter-spacing:.5px;box-shadow:0 6px 6px -4px rgba(0,0,0,.35)}

  .legal{left:76px;top:964px;font-size:8px;line-height:14px;color:var(--navy)}
  .to-top{left:796px;top:962px;width:116px;height:33px;background:var(--panel-head);color:#fff;font-family:"Ubuntu",sans-serif;font-weight:500;font-size:13px;display:flex;align-items:center;justify-content:center;gap:6px;box-shadow:2px 2px 3px rgba(0,0,0,.3)}
</style>
</head>
<body>
<div class="stage">
  <div class="abs card-shadow"></div>
  <div class="abs card"></div>

  <div class="abs brand"><span class="brand-dot"></span>Northvale Petrochem</div>
  <div class="abs system-name">CLEARWAY DESK</div>

  <nav class="abs nav">
    <a class="home" href="#">HOME</a>
    <a class="permits" href="#">PERMITS</a>
    <a class="search" href="#">SEARCH</a>
    <a class="report" href="#">REPORT</a>
    <a class="admin" href="#">ADMIN</a>
    <a class="help" href="#">HELP</a>
  </nav>
  <div class="abs dropdown">
    <div>Create New Permit</div>
    <div class="alt">Transfer Role</div>
    <div>Transfer Res. Person</div>
  </div>

  <div class="abs banner" role="img" aria-label="Banner photo of a petrochemical refinery plant with an official approval stamp on the right"></div>

  <section class="panel" style="left:76px;top:321px;width:407px;height:176px;--cols:133px 144px 1fr">
    <div class="panel-title">New Requests</div>
    <div class="row row-head"><span>Request No.</span><span>Requested Date</span><span>Branch</span></div>
    <div class="row row-body">
      <span><a href="#">56-0003</a><br><a href="#">56-0004</a></span>
      <span class="pad">20/4/2013<br>21/4/2013</span>
      <span class="pad">GC1<br>GC2</span>
    </div>
    <div class="pager"><span class="on">1</span><span>2</span><span>3</span><span>4</span></div>
  </section>

  <section class="panel" style="left:504px;top:321px;width:404px;height:176px;--cols:130px 141px 1fr">
    <div class="panel-title">My Working Requests</div>
    <div class="row row-head"><span>Request No.</span><span>Requested Date</span><span>Status</span></div>
    <div class="row row-body">
      <span><a href="#">56-0003</a><br><a href="#">56-0004</a><br><a href="#">56-0005</a><br><a href="#">56-0006</a></span>
      <span class="pad">20/4/2013<br>21/4/2013<br>20/4/2013<br>21/4/2013</span>
      <span class="pad">Waiting for process<br>In progress<br>Incomplete document<br>Cancel requested</span>
    </div>
    <div class="pager"><span class="on">1</span><span>2</span><span>3</span><span>4</span></div>
  </section>

  <section class="panel" style="left:76px;top:509px;width:832px;height:164px;--cols:133px 141px 142px 143px 140px 1fr">
    <div class="panel-title">Expiring Permits</div>
    <div class="row row-head"><span>Permit No</span><span>Expire Date</span><span>Permit Name</span><span>Branch</span><span>Required Time (day)</span><span>Due Date</span></div>
    <div class="row row-body" style="line-height:16px;padding-top:6px">
      <span><a href="#">AB56001</a><br><a href="#">BIO5502</a></span>
      <span class="pad">25/3/2013<br>24/3/2013</span>
      <span class="pad">Permit Name ###10<br>Permit Name ###20</span>
      <span class="pad">GC1<br>GC2</span>
      <span class="pad">30<br>60</span>
      <span class="pad"><i class="dot red"></i>-40<br><i class="dot amber"></i>-15</span>
    </div>
    <div class="pager"><span class="on">1</span><span>2</span><span>3</span><span>4</span></div>
  </section>

  <section class="panel" style="left:76px;top:684px;width:406px;height:219px;--cols:133px 144px 1fr">
    <div class="panel-title">My In Progress Requests</div>
    <div class="row row-head"><span>Request No.</span><span>Requested Date</span><span>Status</span></div>
    <div class="row row-body">
      <span style="padding-top:2px"><a href="#">56-0001</a><br><a href="#">56-0002</a></span>
      <span class="pad" style="padding-top:2px">20/4/2013<br>21/4/2013</span>
      <span class="pad" style="padding-top:2px">ระหว่างดำเนินการ<br>รอดำเนินการ</span>
    </div>
    <div class="pager"><span class="on">1</span><span>2</span><span>3</span><span>4</span></div>
  </section>

  <div class="abs new-request">
    <svg width="36" height="26" viewBox="0 0 36 26" aria-hidden="true">
      <g fill="#fff">
        <path d="M4 6 L10 0 L24 14 L18 20 Z"/>
        <path d="M19 21 L25 15 L27 23 Z"/>
        <rect x="24" y="22" width="12" height="3"/>
      </g>
    </svg>
    NEW REQUEST
  </div>

  <section class="panel" style="left:501px;top:742px;width:407px;height:161px;--cols:204px 1fr">
    <div class="panel-title">Recent Completed Requests</div>
    <div class="row row-head"><span>Request No.</span><span>Completed Date</span></div>
    <div class="row row-body">
      <span style="padding-top:3px"><a href="#">55-0100</a><br><a href="#">55-0088</a><br><a href="#">55-0002</a></span>
      <span class="pad" style="padding-top:3px">25/3/2013<br>24/3/2013<br>18/1/2013</span>
    </div>
    <div class="pager"><span class="on">1</span><span>2</span><span>3</span><span>4</span></div>
  </section>

  <div class="abs legal">Copyright © 2013 NorthvalePetrochem. All rights reserved.<br>Terms and Condition | Privacy</div>
  <div class="abs to-top">BACK TO TOP
    <svg width="8" height="6" viewBox="0 0 8 6" aria-hidden="true"><path d="M1 5 L4 2 L7 5" stroke="#fff" stroke-width="1.6" fill="none"/></svg>
  </div>
</div>
</body>
</html>
```